Create a banner for me that embodies my health and well being package.

I am an intuitive counselor with a busy practice helping clients to shift their blocks and move forward in their lives.
I have created a package called '9 paths home again'
I am wanting a banner to put on my website page, facebook page and to use as a letter head in mailouts.
My ideal clients are those who want to create change in their lives and who invest money in themselves and their personal and spiritual growth.
I am different to regular life coaches as my sessions have a spiritual twist to them creating much deeper change in my clients.
I would like the banner to be mainly font with the title of the progam: 9 Paths Home Again (no other wording) (something along the lines of the Blackjack font) and that ties in with the theme of my website. I'm not sure what else I want with it and am looking for ideas.
Website:
www.lumorawellspring.com.au
I also have a current facebook page for the business:
https://www.facebook.com/Lumora-Wellspring-Studio-502718364091557/
(Note: I am about to drop my logo and business name and move to using my own name - the rest of the website will remain the same).
I have attached a doc with the draft of what wording will be on the website page any advertising will link to, to give you an idea of what the program is about.

Target Market(s)

People who invest money on themselves who are looking to improve their emotional well being and creating change in their life. Majority are middle aged women (also younger females and some men)

Industry/Entity Type

Health And Wellness

Font styles to use
Other font styles liked:
• I like Blackjack and Amienne. Along those lines.

Requirements
Must have
• Attractive, modern and GREAT font.
Nice to have
• Surprise me with something amazing!
• I love the colours in the 2 images I have up loaded as they represent the heart chakra colours. They could be a feature on the banner or blurred into the background.
Should not have
• Even though my work is quite spiritual I don't want it to look woo woo (meaning airy fairy spiritual stuff!)

```html
<!DOCTYPE html>
<html lang="en">
<head>
<meta charset="utf-8">
<title>9 Paths Home Again — Banner</title>
<link rel="stylesheet" href="https://fonts.googleapis.com/css2?family=Kaushan+Script&display=swap">
<style>
  :root {
    --green-deep: #1f3a0c;
    --green-mid: #3f6a1c;
    --green-soft: #6f9a3a;
    --green-glow: #a8d86a;
    --lotus-pink: #d64a9a;
    --lotus-light: #f08fc4;
    --lotus-dark: #9a2468;
    --title-white: #ffffff;
  }
  html, body {
    margin: 0;
    padding: 0;
    width: 1200px;
    height: 442px;
    overflow: hidden;
    background: var(--green-deep);
  }
  .banner {
    position: relative;
    width: 1200px;
    height: 442px;
    overflow: hidden;
    background:
      radial-gradient(ellipse 420px 300px at 760px 230px, rgba(168,216,106,0.35), transparent 70%),
      linear-gradient(90deg, var(--green-deep) 0%, var(--green-mid) 35%, var(--green-soft) 62%, var(--green-mid) 85%, var(--green-deep) 100%);
  }
  .banner__frame {
    position: absolute;
    inset: 0;
    width: 1200px;
    height: 442px;
  }
  .banner__title {
    position: absolute;
    left: 248px;
    top: 44px;
    width: 320px;
    margin: 0;
    font-family: "Kaushan Script", cursive;
    font-weight: 400;
    color: var(--title-white);
    line-height: 1;
  }
  .banner__title-lead {
    display: block;
    font-size: 86px;
    line-height: 92px;
    white-space: nowrap;
  }
  .banner__title-tail {
    display: block;
    font-size: 56px;
    line-height: 68px;
    white-space: nowrap;
  }
  .banner__lotus {
    position: absolute;
    left: 712px;
    top: 112px;
    width: 246px;
    height: 264px;
    border-radius: 46% 46% 50% 50% / 58% 58% 42% 42%;
    background: radial-gradient(ellipse at 45% 40%, var(--lotus-light) 0%, var(--lotus-pink) 55%, var(--lotus-dark) 100%);
  }
</style>
</head>
<body>
  <main class="banner">
    <svg class="banner__frame" viewBox="0 0 1200 442" aria-hidden="true">
      <defs>
        <linearGradient id="panelLeft" x1="0" y1="0" x2="1" y2="0">
          <stop offset="0" stop-color="#15290a"/>
          <stop offset="0.6" stop-color="#2f5314"/>
          <stop offset="1" stop-color="#1d360b"/>
        </linearGradient>
        <linearGradient id="panelRight" x1="1" y1="0" x2="0" y2="0">
          <stop offset="0" stop-color="#15290a"/>
          <stop offset="0.6" stop-color="#3a6318"/>
          <stop offset="1" stop-color="#1d360b"/>
        </linearGradient>
        <linearGradient id="band" x1="0" y1="0" x2="1" y2="0">
          <stop offset="0" stop-color="#a8d86a" stop-opacity="0.7"/>
          <stop offset="0.5" stop-color="#a8d86a" stop-opacity="0.15"/>
          <stop offset="1" stop-color="#a8d86a" stop-opacity="0.7"/>
        </linearGradient>
      </defs>
      <polygon points="0,0 170,0 232,216 170,442 0,442" fill="url(#panelLeft)"/>
      <polyline points="120,0 182,216 120,442" fill="none" stroke="#a8d86a" stroke-opacity="0.45" stroke-width="3"/>
      <polyline points="150,0 212,216 150,442" fill="none" stroke="#d8f0b0" stroke-opacity="0.5" stroke-width="2"/>
      <polyline points="60,0 122,216 60,442" fill="none" stroke="#a8d86a" stroke-opacity="0.25" stroke-width="10"/>
      <polygon points="1200,0 960,0 1020,216 960,442 1200,442" fill="url(#panelRight)"/>
      <polyline points="1000,0 1060,216 1000,442" fill="none" stroke="#d8f0b0" stroke-opacity="0.5" stroke-width="2"/>
      <polyline points="1040,0 1100,216 1040,442" fill="none" stroke="#a8d86a" stroke-opacity="0.4" stroke-width="6"/>
      <polyline points="1100,0 1160,216 1100,442" fill="none" stroke="#a8d86a" stroke-opacity="0.25" stroke-width="12"/>
      <rect x="0" y="212" width="1200" height="6" fill="url(#band)"/>
      <rect x="0" y="215" width="1200" height="1" fill="#ffffff" fill-opacity="0.35"/>
    </svg>

    <h1 class="banner__title">
      <span class="banner__title-lead">9 Paths</span>
      <span class="banner__title-tail">Home Again</span>
    </h1>

    <div class="banner__lotus" role="img" aria-label="Photograph of a pink lotus bud on its stem against soft green leaves"></div>
  </main>
</body>
</html>
```